Business Card Design for BrightvaleMedia.com

--I need a business card design for my company BrightvaleMedia.com

I have attached my logo...I want the brightvale media logo on the front of the business card, and then I want The Quillstone Chief on the back of it with my information.

I would like to see a light colored background as well as a dark colored background

FRONT:
BRIGHTVALE MEDIA LOGO
248 N. Larkmoor
3rd Floor
San Diego CA 92173
www.BrightvaleMedia.com

Advanced Website & App Development
Websites, Apps, Online Voucher Systems

Leading Edge Marketing Services
SMS, VB, SMM, SEM,

BACK:
QUILLSTONE CHIEF LOGO
Dorian Pelletta
The Quillstone Chief
Call Or Text: 619-555-0148
Dorian@QuillstoneChief.example
www.QuillstoneChief.example

Target Market(s)

small business owners

Industry/Entity Type

Business Consultant

Contact Information for Business Card

FRONT:
BRIGHTVALE MEDIA LOGO
248 N. Larkmoor
3rd Floor
San Diego CA 92173
www.BrightvaleMedia.com

SMS, VB, SMM, SEM,

BACK:
QUILLSTONE CHIEF LOGO
Dorian Pelletta
The Quillstone Chief
Dorian@QuillstoneChief.example
www.QuillstoneChief.example

Requirements
Must have
• add this quote on it somewhere, anywhere,preferrably on back
• "The Fastest Way To Success Is To Take Action”
• — Dorian Pelletta, Quillstone Chief
Nice to have
• open
Should not have
• red

```html
<!DOCTYPE html>
<html lang="en">
<head>
<meta charset="utf-8">
<title>Brightvale Media business cards</title>
<link href="https://fonts.googleapis.com/css2?family=Montserrat:wght@400;500;700&display=swap" rel="stylesheet">
<style>
  :root {
    --brand-blue: #1468a3;
    --ink: #1b1b1b;
    --muted: #666a6e;
    --paper: #ffffff;
    --backdrop: #d6d6d6;
  }
  * { box-sizing: border-box; margin: 0; padding: 0; }
  html, body { width: 1200px; height: 1200px; overflow: hidden; }
  body {
    background: var(--backdrop);
    font-family: "Montserrat", sans-serif;
    position: relative;
  }
  .card {
    position: absolute;
    left: 180px;
    width: 840px;
    height: 480px;
    background: var(--paper);
    overflow: hidden;
    box-shadow: 0 6px 18px rgba(0,0,0,0.18);
  }
  .card--front { top: 90px; }
  .card--back { top: 630px; }

  /* front */
  .services-band {
    position: absolute; left: 0; top: 0;
    width: 380px; height: 84px;
    background: var(--brand-blue);
    border-bottom-right-radius: 44px;
    color: #fff;
    font-weight: 700;
    font-size: 15px;
    line-height: 1.45;
    padding: 16px 0 0 28px;
  }
  .services-note {
    position: absolute; left: 400px; top: 14px;
    font-size: 13px; line-height: 1.35;
    color: var(--muted);
  }
  .wordmark {
    position: absolute;
    font-weight: 500;
    color: var(--brand-blue);
    letter-spacing: 0.12em;
    white-space: nowrap;
  }
  .card--front .wordmark { left: 110px; top: 170px; font-size: 46px; }
  .address {
    position: absolute; left: 500px; top: 300px;
    display: flex; gap: 16px;
    color: var(--muted); font-size: 18px; line-height: 1.45;
  }
  .front-web {
    position: absolute; left: 500px; top: 400px;
    display: flex; align-items: center; gap: 16px;
    color: var(--brand-blue); font-size: 18px;
  }
  .icon { width: 24px; height: 24px; flex: none; fill: var(--brand-blue); }

  /* back */
  .card--back .wordmark { right: 50px; top: 60px; font-size: 40px; }
  .person {
    position: absolute; left: 150px; top: 190px;
  }
  .person__name {
    font-weight: 700; font-size: 26px; color: var(--brand-blue);
    letter-spacing: 0.04em;
  }
  .person__role { font-size: 22px; color: var(--ink); margin-top: 2px; }
  .divider {
    position: absolute; left: 150px; top: 268px;
    width: 370px; height: 1.5px; background: var(--brand-blue);
  }
  .contacts {
    position: absolute; left: 150px; top: 282px;
    list-style: none;
    font-size: 17px; color: var(--muted); line-height: 1.6;
  }
  .contacts li { display: flex; align-items: center; gap: 16px; }
  .contacts .lead { color: var(--brand-blue); }
  .quote-band {
    position: absolute; right: 0; bottom: 0;
    width: 470px; height: 76px;
    background: var(--brand-blue);
    border-top-left-radius: 40px;
    color: #fff;
    font-weight: 500; font-size: 17px;
    display: flex; align-items: center; justify-content: center;
    padding: 0 24px;
  }
</style>
</head>
<body>

<section class="card card--front" aria-label="Card front">
  <div class="services-band">
    Leading Edge Marketing Services<br>SMS, VB, SMM, SEM
  </div>
  <p class="services-note">
    Advanced Website &amp; App Development<br>Websites, Apps, Online Voucher Systems
  </p>
  <div class="wordmark">BRIGHTVALE MEDIA</div>
  <div class="address">
    <svg class="icon" viewBox="0 0 24 24" aria-hidden="true"><path d="M12 3 2 12h3v9h5v-6h4v6h5v-9h3z"/></svg>
    <p>248 N. Larkmoor<br>3rd Floor<br>San Diego CA 92173</p>
  </div>
  <div class="front-web">
    <svg class="icon" viewBox="0 0 24 24" aria-hidden="true"><circle cx="12" cy="12" r="11"/><g fill="none" stroke="#fff" stroke-width="1.3"><circle cx="12" cy="12" r="6.5"/><ellipse cx="12" cy="12" rx="3" ry="6.5"/><path d="M5.5 12h13M6.5 9h11M6.5 15h11"/></g></svg>
    <span>www.BrightvaleMedia.com</span>
  </div>
</section>

<section class="card card--back" aria-label="Card back">
  <div class="wordmark">QUILLSTONE CHIEF</div>
  <div class="person">
    <p class="person__name">DORIAN PELLETTA</p>
    <p class="person__role">The Quillstone Chief</p>
  </div>
  <div class="divider"></div>
  <ul class="contacts">
    <li>
      <svg class="icon" viewBox="0 0 24 24" aria-hidden="true"><path d="M6.6 10.8a15 15 0 0 0 6.6 6.6l2.2-2.2c.3-.3.7-.4 1-.2 1.1.4 2.3.6 3.6.6.6 0 1 .4 1 1V20c0 .6-.4 1-1 1A17 17 0 0 1 3 4c0-.6.4-1 1-1h3.5c.6 0 1 .4 1 1 0 1.3.2 2.5.6 3.600.1.3 0 .7-.2 1z"/></svg>
      <span><span class="lead">Call Or Text:</span> 619-555-0148</span>
    </li>
    <li>
      <svg class="icon" viewBox="0 0 24 24" aria-hidden="true"><path d="M2 5h20v14H2z"/><path d="M2.5 5.5 12 13l9.5-7.5" fill="none" stroke="#fff" stroke-width="1.5"/></svg>
      <span>Dorian@QuillstoneChief.example</span>
    </li>
    <li>
      <svg class="icon" viewBox="0 0 24 24" aria-hidden="true"><circle cx="12" cy="12" r="11"/><g fill="none" stroke="#fff" stroke-width="1.3"><circle cx="12" cy="12" r="6.5"/><ellipse cx="12" cy="12" rx="3" ry="6.5"/><path d="M5.5 12h13M6.5 9h11M6.5 15h11"/></g></svg>
      <span>www.QuillstoneChief.example</span>
    </li>
  </ul>
  <div class="quote-band">“The Fastest Way To Success Is To Take Action”</div>
</section>

</body>
</html>
```